Corvane Holdings , new business card design

investment firm with corporate clients . need double sided business card , vertical and horizontal options ,logo must be clear. prefer pantone colors only and sharp design. website also www.corvane.ae

Khalid Bin Tarrafi
Managing Director
Tel. +971 4 387 2940
Mobile +971 50 518 2403
khalid@corvane.ae
Q-Span Plaza, officw 18-B07, Warqa Gardens, Dubai

Contact Information for Business Card

Khalid Bin Tarrafi
Managing Director

Font styles to use
Serif

Colors

Designer to choose colors to be used in the design.

```html
<!DOCTYPE html>
<html lang="en">
<head>
<meta charset="utf-8">
<title>Corvane Holdings – Business Card</title>
<link rel="stylesheet" href="https://fonts.googleapis.com/css2?family=Roboto+Condensed:wght@700&family=Roboto:wght@300;400;500&display=swap">
<style>
  :root {
    --backdrop: #e7e4df;
    --card-light: #f4f4f4;
    --card-dark: #0b0c10;
    --brand-blue: #4a6f96;
    --ink: #1e1e1e;
    --ink-soft: #4a4a4a;
    --white: #ffffff;
  }
  * { margin: 0; padding: 0; box-sizing: border-box; }
  html, body {
    width: 1200px; height: 960px; overflow: hidden;
    background: var(--backdrop);
  }
  .canvas { position: relative; width: 1200px; height: 960px; }

  .card {
    position: absolute;
    width: 600px; height: 342px;
    box-shadow: 0 2px 6px rgba(0,0,0,0.25);
  }
  .card--front { left: 322px; top: 108px; background: var(--card-light); }
  .card--back  { left: 320px; top: 494px; background: var(--card-dark); }

  .holder { position: absolute; left: 28px; top: 26px; }
  .holder__name {
    font-family: "Roboto Condensed", "Arial Narrow", sans-serif;
    font-weight: 700; font-size: 20px; color: var(--brand-blue);
    text-transform: uppercase; letter-spacing: 0.2px; line-height: 24px;
  }
  .holder__title {
    font-family: "Roboto", Arial, sans-serif;
    font-weight: 500; font-size: 15px; color: var(--ink);
    text-transform: uppercase; line-height: 20px;
  }

  .contacts {
    position: absolute; left: 29px; top: 200px;
    list-style: none;
    font-family: "Roboto", Arial, sans-serif;
    font-size: 14.5px; color: var(--ink-soft);
  }
  .contacts li { display: flex; align-items: center; height: 19px; }
  .contacts svg { width: 13px; height: 13px; margin-right: 7px; fill: var(--brand-blue); flex: none; }

  .brand-name {
    font-family: "Roboto", Arial, sans-serif;
    font-weight: 300; text-transform: uppercase; white-space: nowrap;
  }
  .card--front .brand-name {
    position: absolute; right: 32px; top: 240px;
    font-size: 15px; letter-spacing: 3px; color: var(--ink);
  }
  .card--back .brand-name {
    position: absolute; left: 0; right: 0; top: 150px; text-align: center;
    font-size: 30px; letter-spacing: 8px; color: var(--white);
  }

  .divider {
    position: absolute; left: 28px; top: 287px;
    width: 539px; height: 1px; background: var(--brand-blue);
  }
  .address {
    position: absolute; left: 29px; top: 298px;
    display: flex; align-items: center;
    font-family: "Roboto", Arial, sans-serif;
    font-size: 14px; color: var(--ink-soft);
  }
  .address svg { width: 12px; height: 15px; margin-right: 7px; fill: var(--brand-blue); }
</style>
</head>
<body>
<main class="canvas">
  <section class="card card--front" aria-label="Business card front">
    <div class="holder">
      <p class="holder__name">Khalid Bin Tarrafi</p>
      <p class="holder__title">Managing Director</p>
    </div>

    <ul class="contacts">
      <li>
        <svg viewBox="0 0 24 24" aria-hidden="true"><path d="M6.6 10.8a15.1 15.1 0 0 0 6.6 6.6l2.2-2.2c.3-.3.7-.4 1-.2 1.1.4 2.3.6 3.6.6.6 0 1 .4 1 1V20c0 .6-.4 1-1 1A17 17 0 0 1 3 4c0-.6.4-1 1-1h3.5c.6 0 1 .4 1 1 0 1.3.2 2.5.6 3.6.1.3 0 .7-.2 1z"/></svg>
        +971 4 387 2940
      </li>
      <li>
        <svg viewBox="0 0 24 24" aria-hidden="true"><path d="M7 1h10a2 2 0 0 1 2 2v18a2 2 0 0 1-2 2H7a2 2 0 0 1-2-2V3a2 2 0 0 1 2-2zm0 3v14h10V4zm5 15.5a1.2 1.2 0 1 0 0 2.4 1.2 1.2 0 0 0 0-2.4z"/></svg>
        +971 50 518 2403
      </li>
      <li>
        <svg viewBox="0 0 24 24" aria-hidden="true"><path d="M2 5h20v14H2zm2 2v.4l8 5.2 8-5.2V7zm0 2.8V17h16V9.8l-8 5.2z"/></svg>
        khalid@corvane.ae
      </li>
      <li>
        <svg viewBox="0 0 24 24" aria-hidden="true"><path d="M12 2a10 10 0 1 0 0 20 10 10 0 0 0 0-20zm-1 17.9A8 8 0 0 1 4.2 10.2L9 15v1a2 2 0 0 0 2 2zm6.9-2.5A2 2 0 0 0 16 16h-1v-3a1 1 0 0 0-1-1H8v-2h2a1 1 0 0 0 1-1V7h2a2 2 0 0 0 2-2v-.4a8 8 0 0 1 2.9 12.8z"/></svg>
        www.corvane.ae
      </li>
    </ul>

    <p class="brand-name">Corvane Holdings</p>

    <div class="divider"></div>

    <p class="address">
      <svg viewBox="0 0 24 30" aria-hidden="true"><path d="M12 0a11 11 0 0 0-11 11c0 8 11 19 11 19s11-11 11-19A11 11 0 0 0 12 0zm0 15.5a4.5 4.5 0 1 1 0-9 4.5 4.5 0 0 1 0 9z"/></svg>
      Q-Span Plaza, officw 18-B07, Warqa Gardens, Dubai
    </p>
  </section>

  <section class="card card--back" aria-label="Business card back">
    <p class="brand-name">Corvane Holdings</p>
  </section>
</main>
</body>
</html>
```